Web design for Crowdfunding site HopeWingsRally.com

We need a web design for christian crowdfunding website. Here is the challenge: We need responsive layout that is targeted first in iPad size of screen. It should also scale somehow down to iPhone size of screens. Web layout can be about the same size as iPad screen.

Screens should work so that main page scrolls not but only certain part of the screen scrolls and always one "page" at time. We can implement these "scrolls" then later with javascript but now we need only design. The challenge is to create this kind of hybrid website / app look.

Target is at first to raise funds to orphan people needing about $40 per month for their living and education. There is always some organization which takes care of these kids. Later there will be other christian missions included. At first we are looking to find monthly supporters.

You can be as creative as you want :) As you see from the look and feel sector, I am not looking any same traditional look which many "help kids" sites have. I am looking to reach now younger generation and therefore iPad and mobile are the main screen sizes.

Inspirational designs:
- https://example-gallery.test/profiles/studiofernlake/designs/482716?from=%2Fbrowse%2Fxhr%2Fdesigns%3Fcategory%3Dmobile-app-design
- http://www.artpoolhub.test/design/8261047 Clear, simple visuals
- http://www.artpoolhub.test/design/7394215 Header
- http://www.artpoolhub.test/design/6048392 Contrast in the colors, i think is powerfull

Some terms could be: Kids play, kids are learning (in the school). No static posture but living like kids are. I wonder also how we could also add little bit gaming style even though the question is of reali life of real people. Giving should be rewarding.

Target Market(s)

People who want help other people.

Industry/Entity Type

Christian

Number of Pages Required

4 page

Requirements
Must have
• Homepage. Mission page (In my wireframes it was one kid).
Nice to have
• Other pages and some idea how to scroll. 4 pages is no must. If you feel easy, please give first some draft and I give comments on that.

```html
<!DOCTYPE html>
<html lang="en">
<head>
<meta charset="utf-8">
<title>HopeWingsRally – Mission: Orphan Maria</title>
<link rel="stylesheet" href="https://fonts.googleapis.com/css2?family=Montserrat:wght@400;500;600;700&family=Roboto:wght@300;400&display=swap">
<style>
:root{
  --brand:#ffb000;
  --brand-deep:#ff8a00;
  --ink:#222;
  --text:#444;
  --muted:#9a9a9a;
  --rule:#d6d6d6;
  --row:#f0eff4;
  --tab:#e4e4e4;
  --track:#e8e8e8;
  --footer:#111;
  --white:#fff;
}
*{box-sizing:border-box;margin:0;padding:0}
html,body{width:1200px;height:900px;overflow:hidden;background:var(--white)}
body{position:relative;font-family:"Montserrat",sans-serif;color:var(--ink)}

.site-header{position:absolute;left:0;top:0;width:1200px;height:86px;background:var(--brand);color:var(--white)}
.menu-toggle{position:absolute;left:57px;top:29px;width:35px;height:27px;display:flex;flex-direction:column;justify-content:space-between}
.menu-toggle span{display:block;height:5px;background:var(--white)}
.mission-link{position:absolute;left:107px;top:33px;font-size:16px;font-weight:600;letter-spacing:.2px}
.search-icon{position:absolute;left:269px;top:35px}
.brand-name{position:absolute;left:0;width:1200px;top:22px;text-align:center;font-size:35px;font-weight:700;letter-spacing:.5px}
.login-btn{position:absolute;left:940px;top:22px;width:105px;height:41px;border:1.5px solid var(--white);border-radius:4px;background:var(--brand-deep);font-size:16px;font-weight:500;display:flex;align-items:center;justify-content:center}
.signup-link{position:absolute;left:1076px;top:33px;font-size:16px;font-weight:500}

.story{position:absolute;left:57px;top:110px;width:694px}
.story-title{font-size:22px;font-weight:600}
.tabs{position:absolute;left:2px;top:49px;display:flex;gap:18px}
.tab{width:193px;height:52px;border-radius:4px;background:linear-gradient(#ececec,#dcdcdc);color:#555;font-size:17px;font-weight:600;display:flex;align-items:center;justify-content:center}
.tab.is-active{background:linear-gradient(#ff9a00,#ff7a00);color:var(--white)}

.timeline{position:absolute;left:28px;top:265px;width:4px;height:424px;background:var(--track)}
.timeline-dot{position:absolute;left:-9px;width:22px;height:22px;border-radius:50%;background:var(--track);transform:translateY(-11px)}
.timeline-dot.is-current{background:var(--brand)}

.story-body{position:absolute;left:57px;top:236px;width:694px;font-family:"Roboto",sans-serif;font-weight:300;font-size:16px;line-height:33px;color:var(--text);text-align:justify}
.story-body p{margin-bottom:13px}
.story-photo{display:block;width:692px;height:181px;margin:8px 0 17px 2px;background:linear-gradient(100deg,#b98a6a 0%,#6e7a4a 35%,#9aa080 60%,#5e6a3e 100%)}

.sidebar{position:absolute;left:791px;top:110px;width:352px}
.kid-name{font-size:22px;font-weight:600}
.share{position:absolute;right:0;top:6px;display:flex;gap:12px;align-items:center}
.share-dot{width:12px;height:12px;border-radius:50%;background:var(--muted)}
.meta{position:absolute;top:46px;left:0;width:352px;display:flex;justify-content:space-between;font-size:19px}
.location{color:var(--brand);display:flex;align-items:center;gap:18px;font-weight:500}
.org{color:#333}
.support{position:absolute;top:90px;left:0;width:352px;display:flex;align-items:center;font-size:20px;font-weight:500;color:#333}
.supporters{margin-left:auto;display:flex;gap:13px;align-items:center}
.supporter{width:32px;height:32px;border-radius:50%;border:2px solid #c8c8c8;background:#dcdcdc}
.rule{position:absolute;left:0;width:352px;height:1px;background:var(--rule)}
.support-level{position:absolute;top:160px;font-size:20px;font-weight:600}
.progress{position:absolute;top:209px;left:0}
.progress-label{position:absolute;left:0;top:0;width:160px;height:160px;display:flex;align-items:center;justify-content:center;font-size:38px;font-weight:300;color:#c9c9c9}
.goal{position:absolute;left:170px;top:215px}
.goal-given{font-size:21px;font-weight:500}
.goal-total{font-size:15px;margin-top:6px;color:#333}
.goal-cal{margin-top:24px}
.goal-period{font-size:18px;font-weight:600;color:#333;margin-top:4px}
.participate{position:absolute;top:377px;font-size:20px;font-weight:500;color:#333}
.options{position:absolute;top:433px;left:2px;width:350px;list-style:none}
.option{height:45px;margin-bottom:7px;background:var(--row);display:flex;align-items:center;padding:0 12px;font-size:17px;color:#333}
.option-check{width:33px;height:30px;border-radius:4px;background:var(--brand);margin-right:16px;flex:none}
.option-cart{margin-left:auto}
.amount-field{margin-left:8px;width:138px;height:34px;border:1px dashed #d6d6d6;border-radius:3px;background:var(--white);color:#ccc;font-size:15px;display:flex;align-items:center;padding-left:11px}
.amount-field + .option-cart{margin-left:8px}

.site-footer{position:absolute;left:0;top:836px;width:1200px;height:64px;background:var(--footer);color:#3a3a3a;font-size:16px;font-weight:500;display:flex;align-items:center;justify-content:center}
</style>
</head>
<body>

<header class="site-header">
  <div class="menu-toggle" aria-label="Menu"><span></span><span></span><span></span></div>
  <div class="mission-link">SEE THE MISSION</div>
  <svg class="search-icon" width="16" height="16" viewBox="0 0 16 16" aria-label="Search"><circle cx="6.5" cy="6.5" r="4.5" fill="none" stroke="#fff" stroke-width="2.4"/><line x1="10" y1="10" x2="14.5" y2="14.5" stroke="#fff" stroke-width="2.8" stroke-linecap="round"/></svg>
  <div class="brand-name">HOPEWINGSRALLY</div>
  <div class="login-btn">LOGIN</div>
  <div class="signup-link">SIGNUP</div>
</header>

<section class="story">
  <h1 class="story-title">Mission: Orphan Maria, 11y</h1>
  <nav class="tabs">
    <div class="tab is-active">Our Story</div>
    <div class="tab">Updates</div>
    <div class="tab">Comments</div>
  </nav>
</section>

<div class="timeline">
  <span class="timeline-dot" style="top:0"></span>
  <span class="timeline-dot is-current" style="top:212px"></span>
  <span class="timeline-dot" style="top:424px"></span>
</div>

<article class="story-body">
  <p>Lorem Ipsum is simply dummy text of the printing and typesetting industry. Lorem Ipsum has been the industry's standard dummy text ever since the 1500s, when an unknown printer took a galley of type and scrambled it to make a type specimen book.</p>
  <p>Lorem Ipsum is simply dummy text of the printing and typesetting industry. Lorem Ipsum has been the industry's standard dummy text ever since the 1500s,</p>
  <div class="story-photo" role="img" aria-label="Photo of a group of volunteers gathered outdoors in a green park"></div>
  <p>Lorem Ipsum is simply dummy text of the printing and typesetting industry. Lorem Ipsum has been the industry's standard dummy text ever since the 1500s, when an unknown printer took a galley of type and scrambled it to make a type specimen book.Lorem Ipsum is simply dummy text of the printing and typesetting industry. Lorem Ipsum has been the industry's standard dummy text ever since the 1500s, when an unknown printer took a galley</p>
</article>

<aside class="sidebar">
  <h2 class="kid-name">Name: Maria, 11y</h2>
  <div class="share">
    <svg width="26" height="18" viewBox="0 0 26 18" aria-label="Read"><path d="M1 2h9c2 0 3 1 3 3v12c0-1.5-1-2.5-3-2.5H1zM25 2h-9c-2 0-3 1-3 3v12c0-1.5 1-2.5 3-2.5h9z" fill="none" stroke="#9a9a9a" stroke-width="1.6"/></svg>
    <span class="share-dot"></span><span class="share-dot"></span><span class="share-dot"></span>
  </div>
  <div class="meta">
    <div class="location">
      <svg width="13" height="19" viewBox="0 0 13 19" aria-hidden="true"><path d="M6.5 0C2.9 0 0 2.8 0 6.4 0 11 6.5 19 6.5 19S13 11 13 6.4C13 2.8 10.1 0 6.5 0z" fill="#ffb000"/><circle cx="6.5" cy="6.3" r="2.4" fill="#fff"/></svg>
      Kalkutta
    </div>
    <div class="org">Organization: Jacob</div>
  </div>
  <div class="support">Support
    <div class="supporters">
      <span class="supporter"></span><span class="supporter"></span><span class="supporter"></span><span class="supporter"></span><span class="supporter"></span>
      <svg width="12" height="20" viewBox="0 0 12 20" aria-label="More"><path d="M2 2l8 8-8 8" fill="none" stroke="#c8c8c8" stroke-width="2"/></svg>
    </div>
  </div>
  <div class="rule" style="top:138px"></div>
  <div class="support-level">My support is now:$5 / Month</div>

  <div class="progress">
    <svg width="160" height="160" viewBox="0 0 160 160" aria-label="45% funded">
      <circle cx="80" cy="80" r="68" fill="none" stroke="#e6e6e6" stroke-width="6"/>
      <circle cx="80" cy="80" r="68" fill="none" stroke="#ffb000" stroke-width="6" stroke-dasharray="192.3 427.3" transform="rotate(-90 80 80)"/>
    </svg>
    <div class="progress-label">45%</div>
  </div>
  <div class="goal">
    <div class="goal-given">$15 given</div>
    <div class="goal-total">of total $35 needed</div>
    <svg class="goal-cal" width="17" height="17" viewBox="0 0 17 17" aria-hidden="true"><rect x="1" y="3" width="15" height="13" rx="1" fill="none" stroke="#ffb000" stroke-width="1.6"/><line x1="1" y1="7" x2="16" y2="7" stroke="#ffb000" stroke-width="1.6"/><line x1="5" y1="1" x2="5" y2="5" stroke="#ffb000" stroke-width="1.6"/><line x1="12" y1="1" x2="12" y2="5" stroke="#ffb000" stroke-width="1.6"/><path d="M4 10h2M8 10h2M12 10h1M4 13h2M8 13h2" stroke="#ffb000" stroke-width="1.4"/></svg>
    <div class="goal-period">Per month need</div>
  </div>

  <div class="participate">Participate</div>
  <div class="rule" style="top:421px"></div>
  <ul class="options">
    <li class="option"><span class="option-check"></span>I am in,$1 / month<svg class="option-cart" width="17" height="15" viewBox="0 0 17 15"><path d="M0 1h3l2 8h9l2-6H4" fill="#999" stroke="#999" stroke-width="1.2"/><circle cx="6" cy="13" r="1.5" fill="#999"/><circle cx="13" cy="13" r="1.5" fill="#999"/></svg></li>
    <li class="option"><span class="option-check"></span>Increased, $5 / month<svg class="option-cart" width="17" height="15" viewBox="0 0 17 15"><path d="M0 1h3l2 8h9l2-6H4" fill="#999" stroke="#999" stroke-width="1.2"/><circle cx="6" cy="13" r="1.5" fill="#999"/><circle cx="13" cy="13" r="1.5" fill="#999"/></svg></li>
    <li class="option"><span class="option-check"></span>Decent help,$10 / month<svg class="option-cart" width="17" height="15" viewBox="0 0 17 15"><path d="M0 1h3l2 8h9l2-6H4" fill="#999" stroke="#999" stroke-width="1.2"/><circle cx="6" cy="13" r="1.5" fill="#999"/><circle cx="13" cy="13" r="1.5" fill="#999"/></svg></li>
    <li class="option"><span class="option-check"></span>Whole kid,$35 / month<svg class="option-cart" width="17" height="15" viewBox="0 0 17 15"><path d="M0 1h3l2 8h9l2-6H4" fill="#999" stroke="#999" stroke-width="1.2"/><circle cx="6" cy="13" r="1.5" fill="#999"/><circle cx="13" cy="13" r="1.5" fill="#999"/></svg></li>
    <li class="option"><span class="option-check"></span>My amount<span class="amount-field">Enter Amount</span><svg class="option-cart" width="17" height="15" viewBox="0 0 17 15"><path d="M0 1h3l2 8h9l2-6H4" fill="#999" stroke="#999" stroke-width="1.2"/><circle cx="6" cy="13" r="1.5" fill="#999"/><circle cx="13" cy="13" r="1.5" fill="#999"/></svg></li>
  </ul>
</aside>

<footer class="site-footer">Copyrights@2016Company Name, all rights reserved</footer>

</body>
</html>
```